Name for Roofing Company

We are a company that specialises in supply and installation of metal roofing to Commercial and Domestic buildings in Perth Western Australia. We are looking for someone to come up with a name that is catch innovative and marketable.

```html
<!DOCTYPE html>
<html lang="en">
<head>
<meta charset="utf-8">
<title>Corvane — Name Presentation</title>
<link rel="stylesheet" href="https://fonts.googleapis.com/css2?family=Carlito:wght@400&display=swap">
<style>
  :root {
    --brand-red: #a80000;
    --rule-red: #b01010;
    --ink: #262626;
    --paper-top: #fbfbfb;
    --paper-bottom: #dcdcdc;
  }
  html, body {
    margin: 0;
    padding: 0;
    width: 1200px;
    height: 1200px;
    overflow: hidden;
  }
  .canvas {
    position: relative;
    width: 1200px;
    height: 1200px;
    background: linear-gradient(180deg, var(--paper-top) 0%, #efefef 45%, var(--paper-bottom) 100%);
    overflow: hidden;
  }
  .colour-block {
    position: absolute;
    left: 102px;
    top: 0;
    width: 990px;
    height: 532px;
    background: var(--brand-red);
  }
  .brand-title {
    position: absolute;
    left: 0;
    top: 0;
    width: 1200px;
    height: 1200px;
  }
  .brand-title text {
    font-family: "Carlito", "Calibri", sans-serif;
    font-size: 176px;
    font-weight: 400;
    fill: var(--ink);
  }
  .base-rule {
    position: absolute;
    left: 102px;
    top: 1080px;
    width: 990px;
    height: 3px;
    background: var(--rule-red);
  }
</style>
</head>
<body>
  <main class="canvas">
    <div class="colour-block"></div>
    <svg class="brand-title" viewBox="0 0 1200 1200" aria-label="Corvane">
      <text x="116" y="779">Corvane</text>
    </svg>
    <div class="base-rule"></div>
  </main>
</body>
</html>
```